wardrobe/costume stylist needs good business card for own business

Hi:)

I'm wanting a business card for my company. I am a freelance stylist.

I do wardrobe/costume stylist to TV commercials; Films; Fashion and Lifestyle shoots.

I'd like a design based around my name Rosalind Parfrey written nicely, maybe a colour? Up to you?!

I've attached a couple of images of business cards I like
.... be creative and have fun!

Thank you :)

Reason: I was trying to get my new business card ready for before I headed overseas Friday morning but I don't think that was realistic so I'd like to extend the deadline to give time to the project. Thank you

Hi designers:) Thank you for all your designs, I've extended the deadline until Sunday, so there's a bit more time. I've attached 3 pictures of business cards which I quite like, please take a look to see if it can be of help in your process. I like the pale plain or patterned background with dark font and the dark plain or patterned background with the pale font the motifs the feminine fonts the plain fonts I like the idea of playing with a circle or some shape on one side of the card with my name or initials as in the picture I have on my post could you play around with this idea a bit please? Thank you all for the work you've done :) Rosa

Hi I am working overseas til Saturday night sorry for no feedback until I teturn Thanks :) Rosa

Hi designers, Thank you all so much for submitting your designs, I really appreciate your input into my project :) I'm sorry I didn't get to respond to some comments, and give feedback. I didn't back from being away until later than I expected, and the deadline had passed then, so apologies. Thanks to you all again for all your really good designs :) Rosa

Target Market(s)

I am a freelance stylist my target audience is producers, production companies, photographers, directors...

Industry/Entity Type

Business

Requirements
Must have
• Rosalind Parfrey
Stylist or Wardrobe Stylist

email rosaparfrey@mailbox-example.co.nz
Mobile 0218467193

(Don't have to use the words 'email' and 'mobile')
Nice to have
• Would like it to be double sided
Like B & W
Like pale colour background with dark font or white font
Like dark colour background with pale font
Should not have
• I would prefer it not to incorporate pictures

```html
<!DOCTYPE html>
<html lang="en">
<head>
<meta charset="utf-8">
<title>Rosalind Parfrey – Wardrobe Stylist Business Card</title>
<link rel="stylesheet" href="https://fonts.googleapis.com/css2?family=Pirata+One&family=Open+Sans:wght@400;600&display=swap">
<style>
  :root {
    --backdrop: #d9d6d2;
    --card-white: #f4f3f1;
    --card-black: #0c0c0c;
    --accent-red: #a3161c;
    --accent-red-soft: rgba(163, 22, 28, 0);
    --text-white: #f6f6f6;
    --rule-grey: #8a8a8a;
  }
  * { box-sizing: border-box; margin: 0; padding: 0; }
  html, body {
    width: 1200px;
    height: 900px;
    overflow: hidden;
    background: var(--backdrop);
  }
  .canvas {
    width: 1200px;
    height: 900px;
    display: flex;
    flex-direction: column;
    align-items: center;
    justify-content: center;
    gap: 50px;
  }
  .card {
    position: relative;
    width: 700px;
    height: 400px;
    overflow: hidden;
    box-shadow: 0 6px 18px rgba(0, 0, 0, 0.18);
  }

  /* Contact side */
  .card--contact { background: var(--card-white); color: var(--accent-red); }
  .card--contact .identity {
    position: absolute;
    top: 56px;
    left: 60px;
  }
  .card--contact .name {
    font-family: "Pirata One", cursive;
    font-size: 44px;
    line-height: 1;
    font-weight: 400;
  }
  .card--contact .role {
    font-family: "Open Sans", sans-serif;
    font-size: 13px;
    letter-spacing: 0.04em;
    margin-top: 4px;
    margin-left: 2px;
  }
  .contact-list {
    list-style: none;
    margin-top: 18px;
    font-family: "Open Sans", sans-serif;
    font-size: 19px;
  }
  .contact-list li { display: flex; gap: 30px; margin-bottom: 8px; }
  .contact-list .label { font-weight: 600; width: 16px; margin-left: -36px; }
  .contact-list { padding-left: 36px; margin-left: -36px; }
  .card--contact .ornament {
    position: absolute;
    right: -40px;
    bottom: -40px;
    width: 330px;
    height: 300px;
    background: radial-gradient(ellipse at 70% 65%, var(--accent-red) 0%, rgba(163, 22, 28, 0.45) 40%, var(--accent-red-soft) 72%);
  }

  /* Name side */
  .card--name { background: var(--card-black); color: var(--text-white); }
  .card--name .ornament {
    position: absolute;
    left: -40px;
    top: 20px;
    width: 260px;
    height: 340px;
    background: radial-gradient(ellipse at 35% 50%, var(--accent-red) 0%, rgba(163, 22, 28, 0.45) 40%, var(--accent-red-soft) 72%);
  }
  .card--name .identity {
    position: absolute;
    right: 70px;
    top: 50%;
    transform: translateY(-50%);
    text-align: center;
  }
  .card--name .name {
    font-family: "Pirata One", cursive;
    font-size: 64px;
    line-height: 1;
    font-weight: 400;
  }
  .card--name .rule {
    height: 1px;
    background: var(--rule-grey);
    margin: 8px 0 6px;
  }
  .card--name .role {
    font-family: "Open Sans", sans-serif;
    font-size: 17px;
    letter-spacing: 0.42em;
    padding-left: 0.42em;
  }
  .card--name .identity::after {
    content: "";
    display: block;
    height: 1px;
    background: var(--rule-grey);
    margin-top: 6px;
  }
</style>
</head>
<body>
  <main class="canvas">
    <section class="card card--contact">
      <div class="identity">
        <h1 class="name">Rosalind Parfrey</h1>
        <p class="role">WARDROBE STYLIST</p>
        <ul class="contact-list">
          <li><span class="label">M</span><span class="value">0218467193</span></li>
          <li><span class="label">E</span><span class="value">rosaparfrey@mailbox-example.co.nz</span></li>
        </ul>
      </div>
      <div class="ornament" role="img" aria-label="Red swirling floral flourish ornament"></div>
    </section>

    <section class="card card--name">
      <div class="ornament" role="img" aria-label="Red swirling floral flourish ornament"></div>
      <div class="identity">
        <h2 class="name">Rosalind Parfrey</h2>
        <div class="rule"></div>
        <p class="role">WARDROBE STYLIST</p>
      </div>
    </section>
  </main>
</body>
</html>
```